Medical VIP club - small design

Please read the specs in a design brief attached. Also we don't have logo in a Vector format and attaching the only version we have.

Club

```html
<!DOCTYPE html>
<html lang="en">
<head>
<meta charset="utf-8">
<title>Veridane – Services</title>
<link rel="stylesheet" href="https://fonts.googleapis.com/css2?family=Arimo:wght@400;700&display=swap">
<style>
:root{
  --page-bg:#6b5a41;
  --gold-light:#f2d36a;
  --gold-dark:#c69d2c;
  --brand-brown:#6a4d10;
  --tab-light:#bba98b;
  --tab-dark:#86745a;
  --tab-active-light:#bfc27a;
  --tab-active-dark:#8f8f3c;
  --tab-cta-light:#f6cf45;
  --tab-cta-dark:#c39610;
  --title-light:#a3966c;
  --title-dark:#6b6040;
  --table-head-light:#aba75c;
  --table-head-dark:#7e7832;
  --rule:#c9c9c9;
  --text:#333;
  --white:#fff;
}
*{box-sizing:border-box;margin:0;padding:0}
html,body{width:1200px;height:874px;overflow:hidden}
body{background:var(--page-bg);font-family:"Arimo",Arial,sans-serif;position:relative;color:var(--text)}

.site-header{position:absolute;left:24px;top:10px;width:1158px;height:188px;border-radius:14px;
  background:linear-gradient(180deg,var(--gold-light),var(--gold-dark));overflow:hidden;border:1px solid #a88a3a}
.header-photo{position:absolute;left:440px;top:0;right:0;bottom:0;
  background:linear-gradient(90deg,rgba(201,164,60,1) 0%,rgba(120,140,120,.9) 22%,#5b7f86 40%,#6f8a5a 60%,#4e6a3c 80%,#7d7f70 100%)}
.brand{position:absolute;left:40px;top:62px;display:flex;align-items:center;gap:12px}
.brand-mark{width:34px;height:34px;border-radius:50%;background:var(--brand-brown)}
.brand-name{font-size:56px;font-weight:700;color:var(--brand-brown);line-height:1}
.brand-sub{position:absolute;left:86px;top:124px;font-size:18px;font-weight:700;color:var(--brand-brown)}
.phone{position:absolute;right:18px;top:52px;display:flex;align-items:center;gap:22px}
.phone-icon{width:104px;height:104px}
.phone-number{font-size:48px;font-weight:700;color:var(--white);letter-spacing:-1px;
  text-shadow:0 0 2px #333,0 2px 4px rgba(0,0,0,.6)}

.main-nav{position:absolute;left:24px;top:208px;display:flex;gap:3px}
.main-nav a{width:191px;height:71px;display:flex;align-items:center;justify-content:center;padding-top:8px;
  border-radius:12px 12px 0 0;color:var(--white);text-decoration:none;font-size:20px;
  background:linear-gradient(180deg,var(--tab-light),var(--tab-dark))}
.main-nav a.is-active{background:linear-gradient(180deg,var(--tab-active-light),var(--tab-active-dark))}
.main-nav a.is-cta{background:linear-gradient(180deg,var(--tab-cta-light),var(--tab-cta-dark))}
.nav-band{position:absolute;left:0;top:244px;width:1200px;height:34px;background:linear-gradient(180deg,#efe3cc,#c9b48f);z-index:-1}

.content{position:absolute;left:18px;top:289px;width:1170px;height:485px;background:var(--white);border-radius:12px;overflow:hidden}
.content-title{height:54px;padding-left:32px;display:flex;align-items:center;font-size:24px;color:var(--white);
  background:linear-gradient(180deg,var(--title-light),var(--title-dark))}
.packages{position:absolute;left:31px;top:82px;width:1108px;border-collapse:collapse;font-size:14px}
.packages th{height:34px;color:var(--white);font-size:14px;font-weight:700;border:1px solid var(--rule);
  background:linear-gradient(180deg,var(--table-head-light),var(--table-head-dark))}
.packages td{height:35.3px;padding-left:20px;border:1px solid var(--rule)}
.packages td:not(:first-child){padding-left:14px}
.packages tfoot td{border:none;text-align:center;padding:0;font-weight:700;font-size:14px;height:46px;font-family:"Tinos",Georgia,serif}

.site-footer{position:absolute;left:18px;top:782px;width:1170px;height:85px;border-radius:12px;
  background:linear-gradient(180deg,#f6d865,#e0b21c)}
.social{position:absolute;left:28px;top:26px;display:flex;gap:6px}
.social span{width:38px;height:38px;border-radius:4px}
.social .s1{background:#3b5b96}.social .s2{background:#5ec4e6}.social .s3{background:#e2641d}
.copyright{position:absolute;left:0;right:0;top:38px;text-align:center;font-size:12px;color:#2a2410}
.footer-brand{position:absolute;right:30px;top:22px;display:flex;align-items:center;gap:8px}
.footer-brand .brand-mark{width:22px;height:22px}
.footer-brand .brand-name{font-size:38px}
</style>
</head>
<body>
<header class="site-header">
  <div class="header-photo" role="img" aria-label="Coastal beach town photograph"></div>
  <div class="brand"><span class="brand-mark"></span><span class="brand-name">Veridane</span></div>
  <div class="brand-sub">Veridane Health</div>
  <div class="phone">
    <svg class="phone-icon" viewBox="0 0 104 104" aria-hidden="true">
      <defs><radialGradient id="ph" cx="40%" cy="35%" r="65%"><stop offset="0" stop-color="#e6c27a"/><stop offset="1" stop-color="#7a4f12"/></radialGradient></defs>
      <circle cx="52" cy="52" r="50" fill="url(#ph)" stroke="#5a3a0a" stroke-width="2"/>
      <path d="M22 42 q30-20 60 0 v8 h-14 v-8 q-16-6-32 0 v8 h-14z" fill="#fff"/>
      <path d="M32 52 h40 l8 22 h-56z" fill="#fff"/>
      <circle cx="52" cy="63" r="7" fill="#8a5a1a"/>
    </svg>
    <span class="phone-number">555-010-010</span>
  </div>
</header>

<div class="nav-band"></div>
<nav class="main-nav">
  <a href="#">About Us</a>
  <a href="#">VIP Club</a>
  <a href="#" class="is-active">Services</a>
  <a href="#">Packages &amp; Prices</a>
  <a href="#" class="is-cta">Registration</a>
  <a href="#">Contacts</a>
</nav>

<main class="content">
  <h1 class="content-title">Services</h1>
  <table class="packages">
    <colgroup><col style="width:292px"><col style="width:316px"><col style="width:297px"></colgroup>
    <thead><tr><th>Package 1</th><th>Package 2</th><th>Package 3</th></tr></thead>
    <tbody>
      <tr><td>-Lorem ipsum</td><td>-Lorem ipsum</td><td>-Lorem ipsum</td></tr>
      <tr><td>-Lorem ipsum</td><td>-Lorem ipsum</td><td>-Lorem ipsum</td></tr>
      <tr><td>-Lorem ipsum</td><td>-Lorem ipsum</td><td>-Lorem ipsum</td></tr>
      <tr><td>-Lorem ipsum</td><td>-Lorem ipsum</td><td>-Lorem ipsum</td></tr>
      <tr><td>-Lorem ipsum</td><td>-Lorem ipsum</td><td>-Lorem ipsum</td></tr>
      <tr><td>-Lorem ipsum</td><td>-Lorem ipsum</td><td>-Lorem ipsum</td></tr>
      <tr><td>-Lorem ipsum</td><td>-Lorem ipsum</td><td>-Lorem ipsum</td></tr>
      <tr><td>-Lorem ipsum</td><td>-Lorem ipsum</td><td>-Lorem ipsum</td></tr>
      <tr><td>-Lorem ipsum</td><td>-Lorem ipsum</td><td>-Lorem ipsum</td></tr>
    </tbody>
    <tfoot><tr><td>$000</td><td>$000</td><td>$000</td></tr></tfoot>
  </table>
</main>

<footer class="site-footer">
  <div class="social"><span class="s1"></span><span class="s2"></span><span class="s3"></span></div>
  <p class="copyright">Copyright ©2010 Veridane. All Rights Reserved</p>
  <div class="footer-brand"><span class="brand-mark"></span><span class="brand-name">Veridane</span></div>
</footer>
</body>
</html>
```